larkforge website

commerce website to sell cookeries, brackets, mailboxes and to show off homes built. Modern Steel in design see marlo cycles web page to be like: https://www.marlocycles-demo.com/en/ sorry its bright nest hosting word press divi

must be able to add products to page

Target Market(s)

mainly western states of U.S.

Industry/Entity Type

Building Product

Coding

Coded - Design and coding required

Number of Pages Required

3 page

Font styles to use
Sans Serif

Colors

Designer to choose colors to be used in the design.

Requirements
Must have
• customers to be able to order products from page
• bright nest hosting word press divi

```html
<!DOCTYPE html>
<html lang="en">
<head>
<meta charset="utf-8">
<title>Larkforge</title>
<link href="https://fonts.googleapis.com/css2?family=Roboto:wght@300;400;500;700;900&family=Raleway:wght@400;500&family=Poppins:wght@600;700&display=swap" rel="stylesheet">
<style>
:root{
  --navy:#3c4a7d;
  --navy-dark:#2d3961;
  --ink:#1f2330;
  --text:#555;
  --steel-light:#e4e5e8;
  --steel-mid:#b9bcc3;
  --page:#f1f1f1;
  --footer:#3a3a3c;
  --star:#e07b1a;
  --white:#fff;
  --grill:#2b2c31;
}
*{box-sizing:border-box;margin:0;padding:0}
html,body{width:1200px;height:3921px;overflow:hidden}
body{position:relative;font-family:'Roboto',sans-serif;color:var(--ink);background:var(--page)}
.abs{position:absolute}
.btn{position:absolute;background:var(--navy);color:var(--white);font:700 14px 'Roboto',sans-serif;display:flex;align-items:center;justify-content:center;gap:8px;text-transform:uppercase;border-radius:2px}
.arrow-dot{display:inline-block;width:13px;height:13px;border-radius:50%;background:var(--white);position:relative}
.arrow-dot::after{content:"";position:absolute;left:3px;top:4px;border-left:6px solid var(--navy);border-top:3px solid transparent;border-bottom:3px solid transparent}

/* header */
.topbar{left:0;top:0;width:1200px;height:108px;background:linear-gradient(90deg,#3a4776,#46548a 50%,#3a4776)}
.brand{left:111px;top:38px;color:var(--white);font:500 27px 'Roboto',sans-serif;letter-spacing:1px}
.search{left:515px;top:34px;width:374px;height:41px;background:var(--white);border-radius:21px;font-size:11px;color:#555}
.search .ph{position:absolute;left:12px;top:14px}
.search .cat{position:absolute;left:193px;top:0;height:41px;border-left:1px solid #ddd;padding:13px 12px;font-size:14px;color:#666}
.search .go{position:absolute;right:3px;top:3px;width:35px;height:35px;border-radius:50%;background:var(--navy)}
.cart{left:955px;top:36px;color:var(--white)}
.cart .ring{position:absolute;left:0;top:0;width:40px;height:40px;border:2px solid var(--white);border-radius:50%}
.cart .t{position:absolute;left:54px;top:2px;white-space:nowrap;font-size:13px;line-height:18px}
.navbar{left:0;top:108px;width:1200px;height:53px;background:linear-gradient(90deg,#c8cacf,#e9eaec 50%,#c8cacf)}
.navbar a{position:absolute;top:18px;font:500 15px 'Roboto',sans-serif;color:var(--ink);text-decoration:none}
.navbar a.on{color:var(--navy)}

/* hero */
.hero{left:0;top:161px;width:1200px;height:640px;background:linear-gradient(160deg,#3d5a2f,#6e7d52 40%,#9c8a6e 70%,#3f4a3a)}
.hero-title{left:0;top:318px;width:1200px;text-align:center;color:var(--white);font:700 62px 'Roboto',sans-serif;letter-spacing:1px}
.hero-sub{left:0;top:406px;width:1200px;text-align:center;color:var(--white);font:400 21px 'Roboto',sans-serif}
.slide-arrow{width:42px;height:42px;border:2px solid var(--white);border-radius:50%}

/* section headings */
.eyebrow{font:400 22px 'Roboto',sans-serif;color:#333}
.big{font:300 40px 'Roboto',sans-serif;color:var(--navy)}
.big b{font-weight:900}
.para{font:400 15px/28px 'Raleway',sans-serif;color:var(--text)}

/* products */
.card{position:absolute;top:1563px;width:230px}
.card .img{height:176px;border:1px solid #ddd;background:var(--white);position:relative;overflow:hidden}
.card .img .ph{position:absolute;left:30px;top:22px;width:170px;height:132px;border-radius:6px;background:radial-gradient(ellipse at 50% 40%,#4a4b52 0,var(--grill) 45%,#7d8089 100%)}
.stars{margin:16px 0 0 11px;font-size:10px;color:#555}
.stars span{color:var(--star);letter-spacing:1px;font-size:11px}
.card h4{margin:6px 0 0 11px;font:500 14px 'Roboto',sans-serif;color:var(--ink)}
.card p{margin:6px 0 0 11px;font-size:11px;color:#666}
.card .price{position:absolute;left:11px;top:289px;font:500 15px 'Roboto',sans-serif;color:var(--navy)}
.card .add{position:absolute;left:108px;top:281px;width:112px;height:34px;background:var(--navy);color:var(--white);font-size:12px;display:flex;align-items:center;justify-content:center;border-radius:2px}

/* firepit product area */
.firepit{left:650px;top:2090px;width:430px;height:440px;border-radius:8px;background:linear-gradient(160deg,#b7bccb 0,#8d93a8 35%,var(--grill) 55%,#55575e 80%,#c9ccd3 100%)}

/* news */
.news{position:absolute;top:2770px;width:309px}
.news .img{height:207px}
.news .body{position:absolute;left:15px;top:185px;width:279px;height:185px;background:var(--white);box-shadow:0 3px 10px rgba(0,0,0,.12);padding:20px 20px}
.news h4{font:500 16px 'Roboto',sans-serif;color:var(--ink)}
.news .meta{margin-top:12px;font-size:13px;color:#555;display:flex;gap:26px}
.news .meta i{display:inline-block;width:10px;height:10px;background:var(--navy);margin-right:6px;border-radius:2px}
.news p{margin-top:16px;font:400 14px/23px 'Roboto',sans-serif;color:#666}
.news .more{margin-top:10px;font:700 14px 'Roboto',sans-serif;color:var(--navy);display:flex;align-items:center;gap:8px}
.news .more .arrow-dot{background:var(--navy)}
.news .more .arrow-dot::after{border-left-color:var(--white)}

/* newsletter */
.nl-sub{left:111px;top:3323px;color:var(--white);font:500 16px 'Roboto',sans-serif}
.nl-title{left:111px;top:3354px;color:var(--white);font:700 33px 'Poppins',sans-serif}
.nl-input{left:585px;top:3341px;width:306px;height:46px;background:var(--white);font-size:12px;color:#555;padding:16px 18px}
.nl-btn{left:911px;top:3341px;width:141px;height:46px;background:#262b3f;color:var(--white);font:700 15px 'Roboto',sans-serif;display:flex;align-items:center;justify-content:center}

/* footer */
.f-h{position:absolute;top:3640px;color:var(--white);font:500 17px 'Roboto',sans-serif}
.f-list{position:absolute;top:3682px;list-style:none;color:#e6e6e6;font-size:15px}
.f-list li{height:33px}
.f-list li::before{content:"» ";}
.f-contact{position:absolute;left:340px;top:3682px;color:#e6e6e6;font-size:15px;line-height:21px}
.f-contact div{position:relative;padding-left:19px;margin-bottom:12px}
.f-contact div::before{content:"";position:absolute;left:0;top:5px;width:9px;height:9px;border-radius:50%;background:#e6e6e6}
.f-news{left:821px;top:3686px;width:267px;height:38px;background:var(--white);border-radius:19px;font-size:13px;color:#555;padding:11px 18px}
.f-news .s{position:absolute;right:0;top:0;width:95px;height:38px;background:var(--navy);border-radius:19px;color:var(--white);font:700 14px 'Roboto',sans-serif;display:flex;align-items:center;justify-content:center}
.soc{position:absolute;top:3747px;width:38px;height:38px;border-radius:50%;background:var(--white)}
.rule{left:111px;top:3856px;width:978px;height:1px;background:#8a8a8a}
.copy{left:0;top:3879px;width:1200px;text-align:center;color:#e6e6e6;font-size:15px}
</style>
</head>
<body>

<!-- header -->
<div class="abs topbar"></div>
<div class="abs brand">LARKFORGE</div>
<div class="abs search">
  <span class="ph">Search Product</span>
  <span class="cat">All Categories &#9662;</span>
  <span class="go"><svg width="35" height="35" viewBox="0 0 35 35"><circle cx="16" cy="16" r="5" fill="none" stroke="#fff" stroke-width="2"/><line x1="20" y1="20" x2="24" y2="24" stroke="#fff" stroke-width="2"/></svg></span>
</div>
<div class="abs cart">
  <div class="ring"><svg width="36" height="36" viewBox="0 0 36 36"><path d="M10 12h3l3 9h9l2-6H15" fill="none" stroke="#fff" stroke-width="2"/><circle cx="17" cy="24" r="1.5" fill="#fff"/><circle cx="24" cy="24" r="1.5" fill="#fff"/></svg></div>
  <div class="t"><b style="font-weight:500">MY CART</b><br>0 item- $0.00</div>
</div>

<nav class="abs navbar">
  <a class="on" style="left:108px">Home</a>
  <a style="left:196px">About Us</a>
  <a style="left:305px">Our Products</a>
  <a style="left:442px">Manufacture</a>
  <a style="left:576px">Career</a>
  <a style="left:668px">Clients</a>
  <a style="left:762px">News</a>
  <a style="left:847px">Contact Us</a>
  <a style="left:970px">&#9679; Login/Register</a>
</nav>

<!-- hero -->
<div class="abs hero" role="img" aria-label="Family grilling together on a charcoal kettle grill in a sunny backyard"></div>
<svg class="abs" style="left:0;top:640px" width="1200" height="170" viewBox="0 0 1200 170">
  <polygon points="0,12 600,115 1200,12 1200,48 600,170 0,48" fill="var(--navy)"/>
  <polygon points="0,48 600,170 1200,48 1200,170 0,170" fill="var(--page)"/>
  <polygon points="600,90 636,124 600,163 564,124" fill="var(--navy)"/>
</svg>
<div class="abs hero-title">LARKFORGE</div>
<div class="abs hero-sub">Lorem ipsum dolor sit amet, consectetur adipiscing elit, sed</div>
<div class="btn" style="left:495px;top:470px;width:210px;height:69px;font-size:20px">Shop Now <span class="arrow-dot" style="background:#fff"></span></div>
<div class="abs slide-arrow" style="left:32px;top:404px"><svg width="38" height="38"><polyline points="22,12 15,19 22,26" fill="none" stroke="#fff" stroke-width="2"/></svg></div>
<div class="abs slide-arrow" style="left:1128px;top:404px"><svg width="38" height="38"><polyline points="16,12 23,19 16,26" fill="none" stroke="#fff" stroke-width="2"/></svg></div>

<!-- welcome -->
<svg class="abs" style="left:111px;top:853px" width="385" height="445" viewBox="0 0 385 445" role="img" aria-label="Steel workshop with sparks from metal grinding">
  <defs><linearGradient id="shop" x1="0" y1="0" x2="1" y2="1"><stop offset="0" stop-color="#6a6a6a"/><stop offset=".5" stop-color="#2d2d2d"/><stop offset="1" stop-color="#4a4538"/></linearGradient></defs>
  <polygon points="192,0 385,111 385,334 192,445 0,334 0,111" fill="url(#shop)"/>
</svg>
<div class="abs eyebrow" style="left:597px;top:911px">WELCOME TO</div>
<div class="abs big" style="left:595px;top:936px"><b>LARKFORGE</b></div>
<div class="abs para" style="left:597px;top:1003px;width:493px;text-align:justify">Lorem ipsum dolor sit amet, consectetur adipiscing elit, sed eiusmod tempor incididunt ut labore et dolore magna aliqua. Ut enim ad minim veniam, quis nostrud exercitation ullamco laboris nisi ut aliquip ex ea commodo consequat. Duis aute irure dolor in reprehenderit in voluptate velit esse cillum dolore eu fugiat nulla pariatur.</div>
<div class="btn" style="left:597px;top:1179px;width:158px;height:55px">Learn More <span class="arrow-dot"></span></div>

<!-- feature products -->
<svg class="abs" style="left:0;top:1312px" width="1200" height="772" viewBox="0 0 1200 772">
  <defs><linearGradient id="steel" x1="0" y1="0" x2="1" y2="1"><stop offset="0" stop-color="#c4c6cb"/><stop offset=".45" stop-color="#eeeff1"/><stop offset="1" stop-color="#a9acb3"/></linearGradient></defs>
  <polygon points="0,130 830,5 1200,130 1200,645 370,765 0,645" fill="var(--navy)"/>
  <polygon points="0,146 830,28 1200,115 1200,628 370,742 0,660" fill="url(#steel)"/>
</svg>
<div class="abs big" style="left:0;top:1472px;width:1200px;text-align:center"><b>FEATURE</b> PRODUCTS</div>
<div class="abs slide-arrow" style="left:32px;top:1683px;border-color:#fff"><svg width="38" height="38"><polyline points="22,12 15,19 22,26" fill="none" stroke="#fff" stroke-width="2"/></svg></div>
<div class="abs slide-arrow" style="left:1128px;top:1683px;border-color:#fff"><svg width="38" height="38"><polyline points="16,12 23,19 16,26" fill="none" stroke="#fff" stroke-width="2"/></svg></div>

<div class="card" style="left:111px"><div class="img"><div class="ph" role="img" aria-label="Black kettle charcoal grill on legs"></div></div><div class="stars"><span>★★★★★</span> (20 Reviwes)</div><h4>Lorem ipsum dolor sit amet</h4><p>Sed ut perspiciatis unde omnis</p><div class="price">$ 15.00</div><div class="add">ADD TO CART</div></div>
<div class="card" style="left:361px"><div class="img"><div class="ph" role="img" aria-label="Round charcoal grill with side handles"></div></div><div class="stars"><span>★★★★★</span> (20 Reviwes)</div><h4>Lorem ipsum dolor sit amet</h4><p>Sed ut perspiciatis unde omnis</p><div class="price">$ 15.00</div><div class="add">ADD TO CART</div></div>
<div class="card" style="left:609px"><div class="img"><div class="ph" role="img" aria-label="Steel fire pit bowl filled with logs" style="background:radial-gradient(ellipse at 50% 40%,#6b5440 0,#3a322b 45%,#7d8089 100%)"></div></div><div class="stars"><span>★★★★★</span> (20 Reviwes)</div><h4>Lorem ipsum dolor sit amet</h4><p>Sed ut perspiciatis unde omnis</p><div class="price">$ 15.00</div><div class="add">ADD TO CART</div></div>
<div class="card" style="left:859px"><div class="img"><div class="ph" role="img" aria-label="Rectangular barbecue grill on tall legs"></div></div><div class="stars"><span>★★★★★</span> (20 Reviwes)</div><h4>Lorem ipsum dolor sit amet</h4><p>Sed ut perspiciatis unde omnis</p><div class="price">$ 15.00</div><div class="add">ADD TO CART</div></div>

<!-- manufacturer -->
<div class="abs eyebrow" style="left:111px;top:2162px">MANUFACTURER</div>
<div class="abs big" style="left:109px;top:2187px"><b>FIREPIT</b> COOKERY</div>
<div class="abs para" style="left:111px;top:2254px;width:493px;text-align:justify">Lorem ipsum dolor sit amet, consectetur adipiscing elit, sed eiusmod tempor incididunt ut labore et dolore magna aliqua. Ut enim ad minim veniam, quis nostrud exercitation ullamco laboris nisi ut aliquip ex ea commodo consequat. Duis aute irure dolor in reprehenderit in voluptate velit esse cillum dolore eu fugiat nulla pariatur.</div>
<div class="btn" style="left:111px;top:2430px;width:158px;height:55px">Learn More <span class="arrow-dot"></span></div>
<div class="abs firepit" role="img" aria-label="Black kettle grill with open lid and flames, on a wheeled stand"></div>

<!-- latest news -->
<div class="abs" style="left:0;top:2583px;width:1200px;height:676px;background:var(--white)"></div>
<div class="abs big" style="left:0;top:2685px;width:1200px;text-align:center"><b>LATEST</b> NEWS</div>

<div class="news" style="left:111px"><div class="img" role="img" aria-label="Man grilling food outdoors with friends" style="background:linear-gradient(135deg,#4d6a3a,#9aa6b3 55%,#3f5230)"></div>
  <div class="body"><h4>Sed ut perspiciatis unde omnis</h4><div class="meta"><span><i></i>by Admin</span><span><i></i>Jan 10, 2020</span></div><p>Lorem ipsum dolor sit consectetur adipiscing elit, sed do eiusmod</p><div class="more">READ MORE <span class="arrow-dot"></span></div></div></div>
<div class="news" style="left:445px"><div class="img" role="img" aria-label="Friends gathered around a barbecue in a garden" style="background:linear-gradient(135deg,#7a8c5a,#c8b49a 50%,#5b6b45)"></div>
  <div class="body"><h4>Sed ut perspiciatis unde omnis</h4><div class="meta"><span><i></i>by Admin</span><span><i></i>Dec 27, 2019</span></div><p>Lorem ipsum dolor sit consectetur adipiscing elit, sed do eiusmod</p><div class="more">READ MORE <span class="arrow-dot"></span></div></div></div>
<div class="news" style="left:779px"><div class="img" role="img" aria-label="Cook in an apron holding a tray of grilled meat" style="background:linear-gradient(135deg,#3f5a30,#8a7a6a 50%,#2c2c2c)"></div>
  <div class="body"><h4>Sed ut perspiciatis unde omnis</h4><div class="meta"><span><i></i>by Admin</span><span><i></i>Dec 18, 2019</span></div><p>Lorem ipsum dolor sit consectetur adipiscing elit, sed do eiusmod</p><div class="more">READ MORE <span class="arrow-dot"></span></div></div></div>

<!-- newsletter + footer background -->
<svg class="abs" style="left:0;top:3259px" width="1200" height="662" viewBox="0 0 1200 662">
  <rect x="0" y="0" width="1200" height="662" fill="var(--footer)"/>
  <polygon points="0,0 1200,0 1200,255 600,330 0,255" fill="var(--navy)"/>
  <polygon points="0,255 600,330 1200,255 1200,350 600,305 0,350" fill="var(--white)"/>
  <polygon points="600,218 640,256 600,296 560,256" fill="var(--white)"/>
  <polygon points="600,232 626,256 600,282 574,256" fill="var(--navy)"/>
</svg>
<div class="abs nl-sub">Subscribe Our newsletter to get latest updates</div>
<div class="abs nl-title">Sign UP To Our Newsletter</div>
<div class="abs nl-input">Your Email Address</div>
<div class="abs nl-btn">SUBMIT</div>

<div class="f-h" style="left:111px">Quick Links</div>
<ul class="f-list" style="left:111px"><li>Home</li><li>About Us</li><li>News</li><li>Products</li><li>Contact Us</li></ul>
<div class="f-h" style="left:340px">Contact Us</div>
<div class="f-contact">
  <div>123, Lorem ipsum dolor amet<br>consectetur adipiscing</div>
  <div>(555) 014-2290</div>
  <div>Info@larkforge.com</div>
</div>
<div class="f-h" style="left:632px">Important</div>
<ul class="f-list" style="left:632px;top:3686px"><li>Terms of Use</li><li>Site Map</li><li>Privacy Policy</li><li>Disclaimer</li></ul>
<div class="f-h" style="left:821px">Newsletter Subscription</div>
<div class="abs f-news">Enter your email<div class="s">SUBMIT</div></div>
<div class="soc" style="left:821px"></div>
<div class="soc" style="left:864px"></div>
<div class="soc" style="left:907px"></div>
<div class="soc" style="left:950px"></div>
<div class="abs rule"></div>
<div class="abs copy">© 2020 Larkforge. All Rights Reserved</div>

</body>
</html>
```